International business needs business cards

Our company, DRV Ventures Inc. is in the business of supplying a range construction products with particular emphasis on CEMENT. We have developed our own brand - TORVAN SUPPLIES - with which to infiltrate the market. We are launching our brand of cement (TORVAN Type IS Cement) into the Caribbean which is unlike anything this market has ever seen. A monopoly has existed here for the past 60-odd years and the market has now opened to allow the importation of other brands and consumers are anxious and ready for change/improvement. We are very excited to be launching and want to make a great first impression. We will be conducting workshops and seminars (from government level to the hardware store owners) and we want our business card to give us the strong, confident introduction that we need.

Target Market(s)

construction; builders; engineers; home owners

Industry/Entity Type

Construction

Contact Information for Business Card

Marisol Depree
CEO
cell # 1 555 4180736
Ground floor,Lindell Plaza Suite 2734
George Town,Grand Cayman
Cayman Islands,KY1-4823
EMAIL: m.depree@drvventuresinc.example
web site drvventuresinc.example

COMPANY: skype info drv.ventures.example

second card
Yvette Brannock-Depree
CFO
CELL# 1 555 607 3941
George Town,Grand Cayman
Cayman Islands,KY1-4823
EMAIL: y.brannockdepree@drvventuresinc.example
website drvventuresinc.example

Requirements
Must have
• Business cards must display BOTH logos - DRV is the company and TORVAN is the brand.

```html
<!DOCTYPE html>
<html lang="en">
<head>
<meta charset="utf-8">
<title>DRV Ventures Inc. – Business Card</title>
<link rel="stylesheet" href="https://fonts.googleapis.com/css2?family=Open+Sans:wght@400;600;700&display=swap">
<style>
  :root {
    --backdrop: #2e3034;
    --card: #ffffff;
    --brand-red: #7d161a;
    --panel-blush: #f1e6e6;
    --ink: #111111;
    --text: #222222;
  }
  * { box-sizing: border-box; margin: 0; padding: 0; }
  html, body {
    width: 1200px; height: 864px; overflow: hidden;
    background: var(--backdrop);
    font-family: "Open Sans", Arial, sans-serif;
  }
  .stage { position: relative; width: 1200px; height: 864px; }
  .card {
    position: absolute; left: 320px; width: 560px; height: 320px;
    background: var(--card); overflow: hidden;
  }
  .card--front { top: 92px; }
  .card--back { top: 452px; }

  /* Front */
  .front-wordmark {
    position: absolute; top: 92px; left: 0; right: 0;
    display: flex; justify-content: center; align-items: center; gap: 12px;
  }
  .wordmark-square { width: 52px; height: 52px; background: var(--brand-red); }
  .wordmark-name { font-weight: 700; font-size: 30px; color: var(--ink); letter-spacing: 0.5px; }
  .front-band {
    position: absolute; top: 176px; height: 74px; background: var(--brand-red);
  }
  .front-band--left { left: 0; width: 208px; }
  .front-band--right { left: 306px; width: 254px; }
  .brand-mark {
    position: absolute; top: 176px; left: 208px; width: 98px; height: 74px;
    display: flex; align-items: center; justify-content: center;
    font-weight: 700; font-size: 14px; color: var(--ink); letter-spacing: 1px;
  }

  /* Back */
  .back-panel {
    position: absolute; top: 0; right: 0; width: 342px; height: 100%;
    background: var(--panel-blush);
  }
  .back-content { position: absolute; top: 20px; left: 28px; }
  .back-wordmark { font-weight: 700; font-size: 24px; color: var(--ink); }
  .holder-name { margin-top: 14px; font-weight: 600; font-size: 19px; color: var(--brand-red); }
  .holder-title { font-size: 12px; color: var(--text); }
  .address { margin-top: 18px; font-size: 13.5px; line-height: 19px; color: var(--text); }
  .contact-list { list-style: none; margin-top: 14px; font-size: 13.5px; color: var(--text); }
  .contact-list li { display: flex; align-items: center; gap: 10px; line-height: 21px; }
  .contact-icon { width: 11px; height: 11px; fill: var(--brand-red); flex: none; }
</style>
</head>
<body>
<main class="stage">
  <section class="card card--front" aria-label="Business card front">
    <div class="front-wordmark">
      <span class="wordmark-square"></span>
      <span class="wordmark-name">DRV Ventures Inc.</span>
    </div>
    <div class="front-band front-band--left"></div>
    <div class="brand-mark">TORVAN</div>
    <div class="front-band front-band--right"></div>
  </section>

  <section class="card card--back" aria-label="Business card back">
    <div class="back-panel"></div>
    <div class="back-content">
      <div class="back-wordmark">DRV Ventures Inc.</div>
      <div class="holder-name">Marisol Depree</div>
      <div class="holder-title">CEO</div>
      <address class="address" style="font-style:normal">
        Ground floor, Lindell Plaza Suite 2734<br>
        George Town, Grand Cayman<br>
        Cayman Islands, KY1-4823
      </address>
      <ul class="contact-list">
        <li>
          <svg class="contact-icon" viewBox="0 0 24 24" aria-hidden="true"><path d="M6.6 10.8a15.1 15.1 0 0 0 6.6 6.6l2.2-2.2a1 1 0 0 1 1-.25 11.4 11.4 0 0 0 3.6.57 1 1 0 0 1 1 1V20a1 1 0 0 1-1 1A17 17 0 0 1 3 4a1 1 0 0 1 1-1h3.5a1 1 0 0 1 1 1c0 1.25.2 2.45.57 3.57a1 1 0 0 1-.25 1z"/></svg>
          1 555 4180736
        </li>
        <li>
          <svg class="contact-icon" viewBox="0 0 24 24" aria-hidden="true"><path d="M2 5h20v14H2z M2 5l10 7 10-7" /></svg>
          m.depree@drvventuresinc.example
        </li>
        <li>
          <svg class="contact-icon" viewBox="0 0 24 24" aria-hidden="true"><circle cx="12" cy="12" r="11"/></svg>
          www.drvventuresinc.example
        </li>
      </ul>
    </div>
  </section>
</main>
</body>
</html>
```